Einladungskarten für Firmenjubiläum
Zielgruppe
Ich brauche eine digitale Einladungskarte zum 10-jährigen Firmenjubiläum, das am 12. Juli stattfinden soll. Zu uns; wir sind ein Ingenieurbüro im Bereich Digitalisierung und sicherheitskritische Systeme, wie sie in Flugzeugen, medizinischen Geräten, modernen Autos etc. vorkommen. Autonomes Fahren und Raumfahrtmedizin, sowie Fahrzeugsicherheit und Cyber-Sicherheit gehören z. B. zu unseren Schwerpunktthemen.
Aufgabenstellung
Ich bin für Ideen offen, die sich an dem Inhalt unserer Website anlehnen.

```html
<!DOCTYPE html>
<html lang="de">
<head>
<meta charset="utf-8">
<title>Einladung – 10 Jahre NORVANT Systems</title>
<link rel="stylesheet" href="https://fonts.googleapis.com/css2?family=Montserrat:wght@300;400;600;800&display=swap">
<style>
  :root {
    --navy-top: #0d3a66;
    --navy-mid: #0a2c52;
    --navy-deep: #061a35;
    --cyan: #2fd8f2;
    --cyan-deep: #1aa6e0;
    --white: #ffffff;
  }
  html, body {
    margin: 0;
    padding: 0;
    width: 706px;
    height: 1200px;
    overflow: hidden;
    background: var(--navy-deep);
  }
  .invitation {
    position: relative;
    width: 706px;
    height: 1200px;
    overflow: hidden;
    font-family: "Montserrat", sans-serif;
    color: var(--white);
    background:
      radial-gradient(ellipse 70% 45% at 50% 40%, rgba(40,140,210,0.35), transparent 70%),
      linear-gradient(180deg, var(--navy-top) 0%, var(--navy-mid) 45%, var(--navy-deep) 100%);
  }
  .brand {
    position: absolute;
    top: 104px;
    left: 0;
    width: 100%;
    display: flex;
    justify-content: center;
    align-items: center;
    gap: 12px;
  }
  .brand-mark {
    width: 22px;
    height: 22px;
    background: var(--cyan-deep);
  }
  .brand-name {
    font-weight: 600;
    font-size: 22px;
    letter-spacing: 2px;
    color: var(--white);
  }
  .slogan {
    position: absolute;
    top: 160px;
    left: 0;
    width: 100%;
    text-align: center;
    font-weight: 400;
    font-size: 38px;
    line-height: 1;
    margin: 0;
  }
  .network-globe {
    position: absolute;
    top: 222px;
    left: 60px;
    width: 590px;
    height: 530px;
    border-radius: 50%;
    background:
      radial-gradient(circle at 38% 38%, rgba(120,220,255,0.55) 0%, rgba(40,150,220,0.35) 35%, rgba(15,70,130,0.25) 62%, transparent 72%);
  }
  .jubilee-number {
    position: absolute;
    top: 727px;
    left: 80px;
    margin: 0;
    font-weight: 800;
    font-size: 190px;
    line-height: 1;
    letter-spacing: -4px;
    background: linear-gradient(180deg, var(--cyan) 0%, var(--cyan-deep) 100%);
    -webkit-background-clip: text;
    background-clip: text;
    color: transparent;
  }
  .jubilee-word {
    position: absolute;
    right: 80px;
    margin: 0;
    font-weight: 400;
    font-size: 64px;
    line-height: 1;
  }
  .jubilee-word.years { top: 832px; }
  .jubilee-word.event { top: 892px; }
  .event-date {
    position: absolute;
    top: 984px;
    right: 80px;
    display: flex;
    align-items: center;
    gap: 36px;
    font-weight: 400;
    font-size: 70px;
    line-height: 1;
  }
  .event-date .divider {
    width: 4px;
    height: 64px;
    background: var(--white);
  }
  .event-date .day { color: var(--cyan); font-weight: 300; }
</style>
</head>
<body>
  <main class="invitation">
    <div class="brand">
      <span class="brand-mark"></span>
      <span class="brand-name">NORVANT Systems GmbH</span>
    </div>
    <p class="slogan">Vision.Precision.Safety!</p>

    <div class="network-globe" role="img" aria-label="Leuchtende digitale Weltkugel mit Amerika, umgeben von einem Netz aus verbundenen Lichtpunkten"></div>

    <p class="jubilee-number">10</p>
    <p class="jubilee-word years">jährigen</p>
    <p class="jubilee-word event">Firmenjubiläum</p>

    <div class="event-date">
      <span class="month">Juli</span>
      <span class="divider"></span>
      <span class="day">12</span>
      <span class="divider"></span>
      <span class="year">2024</span>
    </div>
  </main>
</body>
</html>
```